Cover for Lanterns Along the Quiet Shore of Being

Cover for a book that describes everything that happens to a person, from pre-birth life plans through growing in compassion and wisdom to death and living in the afterlife. The information is revealed in messages from people living in the life after this life. The title is Lessons Gathered From Every Season of Your Existence: Shared by Voices Dwelling Beyond the Veil. Author is T. Wesley Prandt. Book size is 6 by 9.

Target Market(s)

General

Font styles to use
Serif

```html
<!DOCTYPE html>
<html lang="en">
<head>
<meta charset="utf-8">
<title>Lessons Gathered From Every Season of Your Existence — Cover</title>
<link rel="stylesheet" href="https://fonts.googleapis.com/css2?family=Alfa+Slab+One&family=Arvo:wght@700&display=swap">
<style>
  :root {
    --page: #efe6da;
    --ink: #37261d;
    --band: #3a2920;
    --band-text: #f4eadf;
    --sky-top: #9aa6b4;
    --sky-pink: #e6c7c0;
    --glow: #fbf0e0;
    --warm: #e9b48a;
    --deep: #c98a62;
  }
  html, body {
    margin: 0;
    width: 1200px;
    height: 995px;
    overflow: hidden;
    background: var(--page);
  }
  .cover {
    position: absolute;
    left: 300px;
    top: 47px;
    width: 600px;
    height: 900px;
    overflow: hidden;
    box-shadow: 0 10px 30px rgba(60, 40, 25, 0.25);
  }
  .cover-art {
    position: absolute;
    inset: 0;
    background:
      radial-gradient(ellipse 60% 35% at 50% 92%, var(--glow) 0%, rgba(251,240,224,0) 70%),
      linear-gradient(180deg, var(--sky-top) 0%, var(--sky-pink) 18%, var(--glow) 40%, var(--warm) 68%, var(--deep) 100%);
  }
  .author {
    position: absolute;
    top: 52px;
    left: 0;
    right: 0;
    margin: 0;
    text-align: center;
    font-family: "Arvo", serif;
    font-weight: 700;
    font-size: 22px;
    letter-spacing: 0.42em;
    color: var(--ink);
  }
  .title {
    position: absolute;
    top: 500px;
    left: 0;
    right: 0;
    margin: 0;
    text-align: center;
    font-family: "Alfa Slab One", serif;
    font-weight: 400;
    color: var(--ink);
    line-height: 1;
  }
  .title .lead { display: block; font-size: 72px; line-height: 0.95; }
  .title .mid { display: block; font-size: 29px; line-height: 1.18; }
  .title .close { display: block; font-size: 64px; line-height: 1; }
  .subtitle {
    position: absolute;
    top: 764px;
    left: 72px;
    right: 72px;
    margin: 0;
    padding: 7px 0 8px;
    background: var(--band);
    color: var(--band-text);
    text-align: center;
    font-family: "Arvo", serif;
    font-weight: 700;
    font-size: 18px;
  }
</style>
</head>
<body>
  <div class="cover">
    <div class="cover-art" role="img" aria-label="Photograph of raised open hands silhouetted against a glowing sunset sky with birds flying upward"></div>
    <p class="author">T. WESLEY PRANDT</p>
    <h1 class="title">
      <span class="lead">LESSONS</span>
      <span class="mid">GATHERED FROM EVERY</span>
      <span class="mid">SEASON OF YOUR</span>
      <span class="close">EXISTENCE</span>
    </h1>
    <p class="subtitle">Shared by Voices Dwelling Beyond the Veil</p>
  </div>
</body>
</html>
```